Dog grooming business card
This is a business card for m dog grooming business like it say above.
In the priorities box below I will have the text that I want on the card.

Industry/Entity Type

Business

Colors

Designer to choose colors to be used in the design.

Requirements
Must have
• My logo and the insurance stamp must be on the card.

Text it must have :

Professional grooming services
Email: lunabrisk@mailvale.net
Text or call 1 705 318 6052
TWF certified/member
Pet first aid certified
Next appointment ___________________________________
Nice to have
• Greens to match my logo

```html
<!DOCTYPE html>
<html lang="en">
<head>
<meta charset="utf-8">
<title>Luna Brisk – Business Card</title>
<link href="https://fonts.googleapis.com/css2?family=Sorts+Mill+Goudy&display=swap" rel="stylesheet">
<style>
  :root {
    --canvas-bg: #e9e6e2;
    --card-white: #ffffff;
    --band-black: #221f20;
    --panel-dark: #3b3637;
    --brand-green: #9dc745;
    --text-dark: #1f1c1d;
    --badge-blue: #3d73b8;
    --rule: #4a4a4a;
  }
  * { margin: 0; padding: 0; box-sizing: border-box; }
  html, body {
    width: 1200px; height: 914px; overflow: hidden;
    background: var(--canvas-bg);
  }
  .canvas {
    position: relative; width: 1200px; height: 914px;
    font-family: "Sorts Mill Goudy", Georgia, serif;
    color: var(--text-dark);
  }
  .card {
    position: absolute; left: 250px; width: 700px; height: 400px;
    background: var(--card-white);
    box-shadow: 0 6px 18px rgba(0,0,0,0.18);
    overflow: hidden;
  }
  .card--back { top: 37px; }
  .card--front { top: 477px; }

  /* back side */
  .band { position: absolute; left: 0; width: 100%; background: var(--band-black); }
  .band--top { top: 0; height: 44px; }
  .band--bottom { bottom: 0; height: 72px; }
  .brand-mark {
    position: absolute; display: flex; align-items: center; gap: 16px;
    color: var(--brand-green); white-space: nowrap;
  }
  .brand-mark__dot {
    width: 54px; height: 54px; border-radius: 50%;
    background: var(--brand-green); flex: none;
  }
  .card--back .brand-mark {
    left: 50%; top: 142px; transform: translateX(-50%);
    font-size: 58px;
  }

  /* front side */
  .logo-panel {
    position: absolute; left: 0; top: 26px; width: 292px; height: 276px;
    background: var(--panel-dark);
    border-radius: 0 16px 16px 0;
  }
  .card--front .brand-mark {
    left: 50%; top: 50%; transform: translate(-50%, -50%);
    font-size: 40px; gap: 12px;
  }
  .card--front .brand-mark__dot { width: 38px; height: 38px; }

  .details {
    position: absolute; left: 300px; top: 40px; width: 390px;
    text-align: center; font-size: 21px; line-height: 1.32;
  }
  .details__contact-note { color: var(--brand-green); }
  .appointment {
    position: absolute; left: 312px; top: 270px; font-size: 21px;
  }
  .appointment__line {
    position: absolute; left: 470px; top: 322px; width: 200px;
    border-top: 1.5px solid var(--rule);
  }
  .insurance-badge {
    position: absolute; left: 478px; top: 336px; width: 176px; height: 54px;
    border: 2px solid var(--badge-blue); border-radius: 14px;
    background: var(--card-white);
  }
</style>
</head>
<body>
<main class="canvas">

  <section class="card card--back" aria-label="Card back">
    <div class="band band--top"></div>
    <div class="brand-mark">
      <span class="brand-mark__dot"></span>
      <span class="brand-mark__name">Luna Brisk</span>
    </div>
    <div class="band band--bottom"></div>
  </section>

  <section class="card card--front" aria-label="Card front">
    <div class="logo-panel">
      <div class="brand-mark">
        <span class="brand-mark__dot"></span>
        <span class="brand-mark__name">Luna Brisk</span>
      </div>
    </div>

    <div class="details">
      <p>Professional grooming services</p>
      <p class="details__contact-note">(Text or call)</p>
      <p>1 705 318 6052</p>
      <p>lunabrisk@mailvale.net</p>
      <p>TWF certified/member</p>
      <p>Pet first aid certified</p>
    </div>

    <p class="appointment">Next appointment</p>
    <div class="appointment__line"></div>

    <div class="insurance-badge" role="img" aria-label="Insurance protection stamp"></div>
  </section>

</main>
</body>
</html>
```